Business Cards Needed for Innovative Healthcare Marketing Company

We are a marketing company focused on healthcare. Our company is all about rebranding yourself renewing your image and generating results. The phoenix stands for "reborn" or "rising" which we provide new brands for our clients we take their old brands and renew it with creativity and innovation. I am looking for a business card with color dimension. I have attached an example of a card I think has the look and feel of what I am trying to accomplish. I like that the card example has black and grey font colors, I like the font placement and the small logo, I really like the use of the colors on the right those are the colors of my logo. My logo is phoenix so maybe incorporating flames similar to that design. I would like the back a solid color maybe red with an opaque version of the logo and website. As a marketing company I am always open to creative liberty!

Target Market(s)

Doctors and business professionals.

Industry/Entity Type

Marketing

Contact Information for Business Card

Valcorne Health Care Marketing
Marla Tenwick- CEO
#(512)638-2974
email-marla@valcorne.com
website- valcorne.com

Font styles to use
Sans Serif

Colors
ec1f27
f37122
ffc214
fbed22
fbf289
f04a50

Requirements
Must have
• The logo and required information
Nice to have
• icons by the information
Should not have
• child like font

```html
<!DOCTYPE html>
<html lang="en">
<head>
<meta charset="utf-8">
<title>Valcorne Health Care Marketing — Business Card</title>
<link rel="stylesheet" href="https://fonts.googleapis.com/css2?family=Josefin+Sans:wght@300&family=Open+Sans:wght@400;600&display=swap">
<style>
  :root {
    --stage: #000000;
    --paper: #f2f2f2;
    --ink: #222222;
    --brand-deep: #9e1b1e;
    --brand-name: #c4401b;
    --flame-top: #f7941d;
    --flame-mid: #d9572a;
    --flame-bottom: #9b1b1f;
    --icon: #e8661f;
    --white: #ffffff;
  }
  * { margin: 0; padding: 0; box-sizing: border-box; }
  html, body {
    width: 1200px; height: 900px; overflow: hidden;
    background: var(--stage);
  }
  .canvas { position: relative; width: 1200px; height: 900px; }

  .card {
    position: absolute; top: 200px;
    width: 310px; height: 502px;
  }
  .card--front {
    left: 265px;
    background: var(--paper);
    border-radius: 62px 0 62px 0;
  }
  .card--back {
    left: 641px; width: 309px;
    background: linear-gradient(180deg, var(--flame-top) 0%, var(--flame-mid) 50%, var(--flame-bottom) 100%);
    border-radius: 0 62px 0 62px;
  }

  .wordmark {
    position: absolute;
    font-family: "Josefin Sans", sans-serif;
    font-weight: 300;
    line-height: 1;
  }
  .wordmark__name { display: block; letter-spacing: 1px; }
  .wordmark__tag { display: block; letter-spacing: 0.6px; }

  .card--front .wordmark {
    right: 25px; top: 202px; text-align: right;
    color: var(--brand-deep);
  }
  .card--front .wordmark__name { font-size: 44px; }
  .card--front .wordmark__tag { font-size: 14.5px; margin-top: 14px; }

  .card--back .wordmark {
    left: 0; right: 0; top: 352px; text-align: center;
    color: var(--white);
  }
  .card--back .wordmark__name { font-size: 52px; }
  .card--back .wordmark__tag { font-size: 18px; margin-top: 20px; }

  .person {
    position: absolute; left: 29px; top: 324px;
    font-family: "Open Sans", sans-serif;
  }
  .person__name { font-size: 19px; font-weight: 600; color: var(--brand-name); line-height: 1.2; }
  .person__role { font-size: 14px; color: var(--ink); margin-top: 3px; }

  .contacts {
    position: absolute; left: 28px; top: 400px;
    list-style: none;
    font-family: "Open Sans", sans-serif;
    font-size: 14.5px; color: var(--ink);
  }
  .contacts__item { display: flex; align-items: center; height: 24px; }
  .contacts__icon { width: 12px; height: 12px; margin-right: 12px; fill: var(--icon); }
</style>
</head>
<body>
<main class="canvas">
  <section class="card card--front" aria-label="Card front">
    <div class="wordmark">
      <span class="wordmark__name">VALCORNE</span>
      <span class="wordmark__tag">HEALTH CARE MARKETING</span>
    </div>

    <div class="person">
      <p class="person__name">Marla Tenwick</p>
      <p class="person__role">CEO</p>
    </div>

    <ul class="contacts">
      <li class="contacts__item">
        <svg class="contacts__icon" viewBox="0 0 12 12" aria-hidden="true"><path d="M2.4 0.6 L4.2 2.6 L3.3 4 C4 5.6 6.3 7.9 8 8.6 L9.4 7.8 L11.4 9.6 L10.2 11.3 C5.8 11.3 0.7 6.2 0.7 1.8 Z"/></svg>
        <span>(512)638-2974</span>
      </li>
      <li class="contacts__item">
        <svg class="contacts__icon" viewBox="0 0 12 12" aria-hidden="true"><path d="M0.5 2.5 H11.5 V10 H0.5 Z M1.2 3.1 L6 6.8 L10.8 3.1" stroke="#f2f2f2" stroke-width="0.9"/></svg>
        <span>marla@valcorne.com</span>
      </li>
      <li class="contacts__item">
        <svg class="contacts__icon" viewBox="0 0 12 12" aria-hidden="true"><circle cx="6" cy="6" r="5.6"/><path d="M3 3.2 C4.5 3.6 5 5 4 6 C5.5 6.8 5 8.6 6 10 M7.6 2 C7.2 3.5 8.4 4 9.8 4.2" stroke="#f2f2f2" stroke-width="0.9" fill="none"/></svg>
        <span>www.valcorne.com</span>
      </li>
    </ul>
  </section>

  <section class="card card--back" aria-label="Card back">
    <div class="wordmark">
      <span class="wordmark__name">VALCORNE</span>
      <span class="wordmark__tag">HEALTH CARE MARKETING</span>
    </div>
  </section>
</main>
</body>
</html>
```